Business Card Design

Our Pharmacy Opens late - the last to close in Brisbane
over 30 years since opened.
Open from 7am - 11pm every day.
Next to Corbel 7 Day Medical Centre
Parking in front of shop
Sit with a pharmacist for every script - the best advice every time.
Private consulting room.
We have the medication that you need.
Wide range Home Health Care products.

Looking for a card that my (young) staff feel happy to hand out to people they they meet.
Updates

Hello Many thanks for your submissions I just need to clarify the costings for this project as per my updated brief Please confirm then we can proceed Many thanks Clive

Reason: due to the adjusted brief and query I have extended the deadline Many thanks for those that have submitted, I will choose the designer as soon as I understand the costings of the project, as per the message despatched today Regards clive

Target Market(s)

men and women 30-70

Industry/Entity Type

Business

Contact Information for Business Card

Meltons Pharmacy - Corbel
317 Galloway Rd
Corbel 4187
Last to Close
Open 7am - 11pm

Font styles to use
Sans Serif

Requirements
Must have
• each batch of 250 will have the following staff names

Doreen Vallow, Senior Pharmacist
Lucia Tomba, Pharmacist
Wu Lan, Pharmacist
Odalie Brunskill, Pharmacist
Greta Lounds, Retail Manager
Joy Mettrick, Marketing Manager
Clive Melton, Pharmacist Proprietor
Should not have
• Please advise if the cost of this job covers the 7 individualised business cards.

Each staff member needs their own card.

please advise

```html
<!DOCTYPE html>
<html lang="en">
<head>
<meta charset="utf-8">
<title>Meltons Pharmacy – Business Card</title>
<link rel="stylesheet" href="https://fonts.googleapis.com/css2?family=Open+Sans:wght@400;600;700&display=swap">
<style>
  :root {
    --bg: #e9e7e4;
    --card: #ffffff;
    --navy: #2b2f8a;
    --navy-soft: #3f4596;
    --ink: #3a3a3a;
    --yellow: #f2ea1c;
    --yellow-edge: #d9cf10;
  }
  * { margin: 0; padding: 0; box-sizing: border-box; }
  html, body {
    width: 1200px; height: 959px; overflow: hidden;
    background: var(--bg);
    font-family: "Open Sans", Arial, sans-serif;
  }
  .canvas { position: relative; width: 1200px; height: 959px; }
  .card {
    position: absolute; left: 100px; top: 194px;
    width: 1000px; height: 571px;
    background: var(--card);
    box-shadow: 0 10px 30px rgba(0,0,0,0.12);
    overflow: hidden;
  }
  .tab {
    position: absolute; width: 44px; height: 110px;
    background: linear-gradient(90deg, var(--yellow-edge), var(--yellow));
    border-radius: 10px;
  }
  .tab--left { left: -18px; top: 300px; }
  .tab--right { right: -18px; top: 110px; }

  .brand {
    position: absolute; left: 90px; top: 250px;
    display: flex; align-items: center; gap: 16px;
  }
  .brand__dot {
    width: 46px; height: 46px; border-radius: 50%;
    background: var(--yellow);
  }
  .brand__name {
    font-weight: 700; font-size: 34px; color: var(--navy);
    line-height: 1.1; letter-spacing: 0.5px;
  }

  .divider {
    position: absolute; left: 486px; top: 160px;
    width: 4px; height: 260px; background: var(--navy);
  }
  .details { position: absolute; left: 520px; top: 162px; width: 430px; }
  .person__name {
    font-weight: 700; font-size: 26px; color: var(--navy-soft);
    letter-spacing: 0.5px; text-transform: uppercase;
  }
  .person__role { font-size: 19px; color: var(--ink); margin-top: 2px; }
  .contact { list-style: none; margin-top: 38px; }
  .contact__item {
    display: flex; align-items: center; gap: 14px;
    font-size: 23px; color: var(--ink); margin-bottom: 12px;
    white-space: nowrap;
  }
  .contact__icon { width: 24px; height: 24px; flex: none; }
</style>
</head>
<body>
<div class="canvas">
  <section class="card">
    <div class="tab tab--left"></div>
    <div class="tab tab--right"></div>

    <div class="brand">
      <span class="brand__dot"></span>
      <span class="brand__name">Meltons<br>Pharmacy</span>
    </div>

    <div class="divider"></div>

    <div class="details">
      <p class="person__name">Doreen Vallow</p>
      <p class="person__role">Senior Pharmacist</p>
      <ul class="contact">
        <li class="contact__item">
          <svg class="contact__icon" viewBox="0 0 24 24"><circle cx="12" cy="12" r="12" fill="#3f4596"/><path d="M12 5a4.5 4.5 0 0 0-4.5 4.5C7.5 13 12 18.5 12 18.5s4.5-5.5 4.5-9A4.5 4.5 0 0 0 12 5z" fill="#fff"/><circle cx="12" cy="9.5" r="1.6" fill="#3f4596"/></svg>
          317 Galloway Rd, Corbel 4187
        </li>
        <li class="contact__item">
          <svg class="contact__icon" viewBox="0 0 24 24"><circle cx="12" cy="12" r="12" fill="#3f4596"/><circle cx="12" cy="12" r="6" fill="none" stroke="#fff" stroke-width="1.6"/><path d="M12 8.5V12l2.5 1.8" stroke="#fff" stroke-width="1.6" fill="none" stroke-linecap="round"/></svg>
          Open 7am – 11pm every day
        </li>
        <li class="contact__item">
          <svg class="contact__icon" viewBox="0 0 24 24"><circle cx="12" cy="12" r="12" fill="#3f4596"/><path d="M7.5 12.5l3 3 6-6.5" stroke="#fff" stroke-width="2" fill="none" stroke-linecap="round" stroke-linejoin="round"/></svg>
          Last to Close
        </li>
      </ul>
    </div>
  </section>
</div>
</body>
</html>
```